Garlic Farm for Farm Sales/Restaurant sales

Need a professional, but appealing to agriculture world. We are selling 27 kinds of Organic Garlic from a farm in Simla,CO. I have uploaded logo and business information-we are going to need a template, because I will need to use it for four separate people.
-We are trying to appeal to Farm to table restaurants
-As well as growers/farmers

Target Market(s)

Agriculture Sales/Restaurants-Organic

Industry/Entity Type

Agriculture

Contact Information for Business Card

Want it to look more unique then your average kelto stock card- I want it to look amazing

Font styles to use
Sans Serif

Colors
0455a3
ec1f27
fbed22
ffffff

Requirements
Must have
• Just be creative
Nice to have
• Colorful
Should not have
• plain

```html
<!DOCTYPE html>
<html lang="en">
<head>
<meta charset="utf-8">
<title>Summit Field Garlic – Business Cards</title>
<link rel="stylesheet" href="https://fonts.googleapis.com/css2?family=Questrial&display=swap">
<style>
  :root {
    --brand-blue: #0455a3;
    --brand-navy: #2a3f8f;
    --brand-red: #e0223c;
    --brand-yellow: #fbed22;
    --card-white: #ffffff;
    --backdrop: #e8e4dd;
    --edge-shadow: rgba(40, 30, 20, 0.18);
  }
  * { box-sizing: border-box; margin: 0; padding: 0; }
  html, body {
    width: 1200px;
    height: 858px;
    overflow: hidden;
    background: var(--backdrop);
    font-family: "Questrial", "Century Gothic", sans-serif;
  }
  .stage {
    position: relative;
    width: 1200px;
    height: 858px;
  }
  .card {
    position: absolute;
    top: 280px;
    width: 520px;
    height: 297px;
    background: var(--card-white);
    box-shadow: 0 10px 26px var(--edge-shadow);
    overflow: hidden;
  }
  .card--front { left: 40px; }
  .card--back { left: 640px; }

  /* Front */
  .front-logo {
    position: absolute;
    left: 34px;
    top: 92px;
    width: 200px;
    display: flex;
    align-items: center;
    gap: 12px;
  }
  .front-logo__dot {
    flex: none;
    width: 46px;
    height: 46px;
    border-radius: 50%;
    background: var(--brand-red);
  }
  .front-logo__name {
    color: var(--brand-navy);
    font-size: 25px;
    line-height: 1.05;
  }
  .divider {
    position: absolute;
    left: 252px;
    top: 0;
    width: 1.5px;
    height: 246px;
    background: var(--brand-red);
  }
  .person {
    position: absolute;
    left: 290px;
    top: 34px;
  }
  .person__name {
    color: var(--brand-red);
    font-size: 24px;
    letter-spacing: 0.3px;
  }
  .person__role {
    color: var(--brand-navy);
    font-size: 12.5px;
    margin-top: 2px;
  }
  .contact {
    position: absolute;
    left: 290px;
    top: 160px;
    color: var(--brand-navy);
    font-size: 14px;
    line-height: 27px;
    list-style: none;
  }
  .tagline-band {
    position: absolute;
    left: 0;
    bottom: 0;
    width: 100%;
    height: 40px;
    background: var(--brand-red);
    color: var(--card-white);
    font-size: 12.5px;
    display: flex;
    align-items: center;
    justify-content: center;
    letter-spacing: 0.2px;
  }

  /* Back */
  .back-mark {
    position: absolute;
    left: 0;
    top: 0;
    width: 100%;
    height: 100%;
    display: flex;
    flex-direction: column;
    align-items: center;
    justify-content: center;
    gap: 18px;
  }
  .back-mark__dot {
    width: 86px;
    height: 86px;
    border-radius: 50%;
    background: var(--brand-red);
  }
  .back-mark__name {
    color: var(--brand-navy);
    font-size: 40px;
    letter-spacing: 3px;
    text-transform: uppercase;
  }
  .back-mark__sub {
    color: var(--brand-red);
    font-size: 18px;
    letter-spacing: 2px;
    text-transform: uppercase;
    margin-top: -10px;
  }
</style>
</head>
<body>
<main class="stage">
  <section class="card card--front" aria-label="Business card front">
    <div class="front-logo">
      <span class="front-logo__dot"></span>
      <span class="front-logo__name">summit field garlic</span>
    </div>
    <div class="divider"></div>
    <div class="person">
      <p class="person__name">Ravi Menon</p>
      <p class="person__role">Reiki Master (Tibetan Usui)</p>
    </div>
    <ul class="contact">
      <li>+61 400 555 019</li>
      <li>ravi.menon@example.com</li>
      <li>PO Box 112, Perth Australia</li>
    </ul>
    <p class="tagline-band">“Using Universal Energy for Conscious Healing and Personal Growth”</p>
  </section>

  <section class="card card--back" aria-label="Business card back">
    <div class="back-mark">
      <span class="back-mark__dot"></span>
      <p class="back-mark__name">Summit Field</p>
      <p class="back-mark__sub">Gourmet Garlic</p>
    </div>
  </section>
</main>
</body>
</html>
```